Web site for a company that sells Pinball machines

We need a website that is an online shopping experience for a Store that sells pinball machines and accessories. The name of the store is called "Gadget Arcade." The store it self has a showroom, but we would also like to have an Internet e-commerce presence. We pinball machines made by Vexler pinball. You can visit their website and see their current list of machines as well as their website for the machines that we are going to carry in our store. Their website is Vexlerpinball.com. I am able to use their machine photos as well as their machine brochure PDF files. I am also able to use their logo on my website two list it as a Vexler Authorized Dealer.
This website design needs to be funky, fun, very technologically oriented and modern. The people buying machines our spending anywhere between $5000 and $15,000 on one machine. These Are high-end buyers who are also usually fairly tech savvy or at least enjoy technology and graphics.
Attachments: I have attached photographs of some of my own machines which may be used in the website. I've also attached some downloaded files from Vexler pinball.com as well as some of their PDF files for brochures. I will carry all of their current models they have listed under games. Not the archived games. I have included one of their machines called Thunderwolf Limited edition in my photograph attachments. The rest of the photos are just random pictures that I have taken myself and maybe used to build the site. Lastly I have attached my logo which I am not super crazy about so I will also be posting a contest to redesign this logo. Tons more of my own pinball photos are available.
I would like for people to be able to purchase machines and accessories from the website, but also inform them to our actual showroom.
Updates
Project Deadline Extended Reason: Hello. We have extended five days due to some complications during the construction of our actual building. We were unable to participate in this web design during this time and so unfortunately were not able give feedback appropriately. We are back on track and will provide feedback to the designers who have designed up until this point. We will still be interested in seeing new submissions, however; this extension will give us a chance to provide feedback and coordinate the website appropriately. Thank you so much for your submissions and your patience!!!!Gadget Arcade Added Friday, April 21, 2017
Target Market(s)
Target market is 16 to 75. Techy individuals to enjoy gaming technology video animation and Vegas style twinkle
Industry/Entity Type
It Company
Coding
Coded - Design and coding required
Number of Pages Required
3 page
Font styles to use
Look and feel
Each slider illustrates characteristics of the customer's brand and the style your logo design should communicate.

```html
<!DOCTYPE html>
<html lang="en">
<head>
<meta charset="utf-8">
<title>Gadget Arcade – Pinball Machines</title>
<link rel="stylesheet" href="https://fonts.googleapis.com/css2?family=Raleway:wght@400;500;600;700;800&family=Open+Sans:wght@400;600;700&display=swap">
<style>
:root{
  --purple:#4a2596;
  --purple-dark:#3a1c7a;
  --ink:#333333;
  --muted:#555555;
  --line:#e3e3e3;
  --band:#f1f1f1;
  --white:#ffffff;
  --frame:#6d6d6d;
}
*{box-sizing:border-box;margin:0;padding:0}
html,body{width:1200px;height:2711px;overflow:hidden}
body{font-family:"Open Sans",Arial,sans-serif;color:var(--ink);background:var(--white);position:relative}
.wrap{position:absolute;left:161px;width:878px}

/* top bar */
.topbar{position:absolute;top:0;left:0;width:1200px;height:40px;background:var(--purple)}
.topbar ul{position:absolute;right:161px;top:12px;display:flex;list-style:none;font-size:12px;color:#fff}
.topbar li{padding:0 12px;border-left:1px solid rgba(255,255,255,.7);line-height:14px}
.topbar li:first-child{border-left:0}
.topbar li:last-child{padding-right:2px}

/* header */
.header{position:absolute;top:40px;left:0;width:1200px;height:119px;background:#fff}
.brand{position:absolute;left:161px;top:30px;display:flex;align-items:center;gap:10px}
.brand .dot{width:46px;height:46px;border-radius:50%;background:var(--purple)}
.brand span{font-family:"Raleway",sans-serif;font-weight:800;font-size:22px;color:var(--purple);line-height:1.05;width:100px}
.search{position:absolute;left:596px;top:27px;width:244px;height:32px;background:#f2f2f2;display:flex;align-items:center;padding:0 14px;font-size:10px;font-style:italic;color:#777;justify-content:space-between}
.basket{position:absolute;left:855px;top:27px;width:180px;height:32px;background:var(--purple);color:#fff;font-size:10.5px;font-weight:600;display:flex;align-items:center;justify-content:center;gap:5px}
.nav{position:absolute;left:386px;top:84px;width:653px;display:flex;justify-content:space-between;font-size:12.5px;font-weight:600;color:#222;letter-spacing:.2px}
.nav .active{color:var(--purple);position:relative}
.nav .active:after{content:"";position:absolute;left:0;right:0;bottom:-22px;height:3px;background:var(--purple)}

/* hero */
.hero{position:absolute;top:159px;left:0;width:1200px;height:473px;background:linear-gradient(110deg,#3a2a3c 0%,#7a3c46 25%,#4a4a66 45%,#8a8790 65%,#3d3a44 100%)}
.hero h1{position:absolute;left:163px;top:193px;font-family:"Raleway",sans-serif;font-weight:800;font-size:40px;line-height:40px;color:#fff;text-transform:uppercase}
.hero .arrow{position:absolute;top:210px}

/* features */
.features{position:absolute;top:632px;left:0;width:1200px;height:154px;background:var(--band)}
.feature{position:absolute;top:24px;width:278px;height:100px;background:#fff;border:1px solid #e2e2e2;display:flex;align-items:center;padding-left:24px;gap:22px}
.feature h3{font-family:"Raleway",sans-serif;font-weight:500;font-size:23px;color:var(--purple);margin-bottom:4px}
.feature p{font-size:10px;color:#444}

/* featured products */
.section-title{position:absolute;top:818px;left:0;width:1200px;text-align:center;font-family:"Raleway",sans-serif;font-weight:700;font-size:23px;color:#333}
.grid{position:absolute;top:884px;left:161px;width:878px;display:grid;grid-template-columns:repeat(4,206px);column-gap:18px;row-gap:22px}
.card{height:278px;border:1px solid var(--line);background:#fff;text-align:center}
.card .photo{height:190px;border-bottom:1px solid var(--line);display:flex;align-items:center;justify-content:center}
.card .photo div{width:70px;height:164px;background:linear-gradient(180deg,#2f2a55,#4f3f8a 40%,#2b2340)}
.card .photo div.wide{width:114px;height:170px;background:linear-gradient(160deg,#5a3d8a,#c24a4a 45%,#3b6fa8)}
.card .photo div.side{width:100px;height:150px;background:linear-gradient(180deg,#3a3652,#5b5a7a 40%,#23202e)}
.card h4{font-weight:400;font-size:12px;color:#333;line-height:18px;margin-top:10px}
.card .price{font-family:"Raleway",sans-serif;font-weight:700;font-size:16px;color:var(--purple);margin-top:10px}

/* latest */
.latest{position:absolute;top:1538px;left:0;width:1200px;height:406px;background:linear-gradient(100deg,#231733 0%,#3c2a55 30%,#2a2234 55%,#5a2b3e 80%,#2d1e2c 100%)}
.latest svg{position:absolute;left:0;top:0}
.latest .text{position:absolute;left:161px;top:108px;width:370px;color:#fff}
.latest h2{font-family:"Raleway",sans-serif;font-weight:700;font-size:28px;margin-bottom:14px}
.latest p{font-size:12px;line-height:21px}
.latest .price{font-family:"Raleway",sans-serif;font-weight:700;font-size:22px;margin-top:16px}
.machine{position:absolute;left:746px;top:52px;width:220px;height:314px;background:linear-gradient(180deg,#2b2f47,#4a5378 35%,#6a7390 60%,#1e2030)}
.dots{position:absolute;left:802px;top:378px;display:flex;gap:4px}
.dots i{width:6px;height:6px;border-radius:50%;background:#222}
.dots i:first-child{background:var(--purple)}

/* buy */
.buy{position:absolute;top:1996px;left:0;width:1200px;text-align:center}
.buy h2{font-family:"Raleway",sans-serif;font-weight:700;font-size:30px;color:var(--purple)}
.buy p{width:880px;margin:22px auto 0;font-size:10.5px;line-height:19px;color:#222}
.btn{display:inline-block;margin-top:20px;width:166px;height:43px;line-height:43px;border-radius:22px;background:var(--purple);color:#fff;font-weight:700;font-size:12.5px}

/* footer */
.footer{position:absolute;top:2291px;left:0;width:1200px;height:420px;background:var(--band);border-top:1px solid #cfcfcf}
.newsletter{position:absolute;top:2246px;left:161px;width:878px;height:90px;border:7px solid var(--frame);background:#fff;display:flex;align-items:center;padding:0 12px 0 10px}
.newsletter h3{font-family:"Raleway",sans-serif;font-weight:700;font-size:17.5px;color:var(--purple);width:392px}
.newsletter .field{width:358px;height:36px;border:1px solid #ccc;font-size:10px;font-style:italic;color:#555;display:flex;align-items:center;padding-left:14px}
.newsletter .join{width:68px;height:36px;background:var(--purple);color:#fff;font-size:11px;font-weight:700;display:flex;align-items:center;justify-content:center}
.col{position:absolute;top:2382px}
.col h4{font-family:"Raleway",sans-serif;font-weight:700;font-size:13px;color:#222;margin-bottom:14px}
.col ul{list-style:none;font-size:10.5px;line-height:20px;color:#333}
.dealer{position:absolute;left:826px;top:2418px;display:flex;align-items:center;gap:8px}
.dealer i{width:26px;height:26px;border-radius:50%;background:#c9c9c9}
.dealer span{font-family:"Raleway",sans-serif;font-weight:700;font-size:19px;color:#bdbdbd}
.follow{position:absolute;left:819px;top:2503px}
.follow h4{font-family:"Raleway",sans-serif;font-weight:700;font-size:13px;color:#222;margin-bottom:12px}
.follow div{display:flex;gap:8px}
.follow i{width:18px;height:18px;border-radius:50%;border:1px solid #555;display:block}
.rule{position:absolute;top:2638px;left:161px;width:878px;height:1px;background:#dcdcdc}
.legal{position:absolute;top:2664px;left:0;width:1200px;text-align:center;font-size:10px;color:#222}
.legal span{padding:0 9px;border-left:1px solid #333}
.legal span:first-child{border-left:0}
.legal .chat{color:var(--purple)}
</style>
</head>
<body>

<div class="topbar"><ul><li>Login/Register</li><li>Wishlist</li><li>My Account</li></ul></div>

<header class="header">
  <div class="brand"><div class="dot"></div><span>Gadget Arcade</span></div>
  <div class="search">Enter Keyword..
    <svg width="11" height="11" viewBox="0 0 12 12"><circle cx="5" cy="5" r="3.8" fill="none" stroke="#222" stroke-width="1.8"/><line x1="8" y1="8" x2="11" y2="11" stroke="#222" stroke-width="2"/></svg>
  </div>
  <div class="basket">
    <svg width="11" height="10" viewBox="0 0 12 11"><path d="M0 1h2.5l1.6 6h6.2l1.4-4.5H3.4" fill="none" stroke="#fff" stroke-width="1.4"/><circle cx="5" cy="9.5" r="1.1" fill="#fff"/><circle cx="9.5" cy="9.5" r="1.1" fill="#fff"/></svg>
    VIEW BASKET / CHECKOUT</div>
  <nav class="nav"><span class="active">HOME</span><span>ABOUT US</span><span>ALL PRODUCTS</span><span>COMMUNITY</span><span>SUPPORT</span><span>CONTACT</span></nav>
</header>

<section class="hero" role="img" aria-label="Close-up photo of a pinball playfield with a chrome ball in an arcade">
  <svg class="arrow" style="left:40px" width="30" height="56" viewBox="0 0 30 56"><polyline points="26,2 4,28 26,54" fill="none" stroke="#fff" stroke-width="2"/></svg>
  <h1>We will buy<br>your machine!</h1>
  <svg class="arrow" style="left:1128px" width="30" height="56" viewBox="0 0 30 56"><polyline points="4,2 26,28 4,54" fill="none" stroke="#fff" stroke-width="2"/></svg>
</section>

<section class="features">
  <div class="feature" style="left:161px">
    <svg width="22" height="40" viewBox="0 0 22 40"><rect x="1.5" y="1.5" width="19" height="37" rx="3" fill="none" stroke="#444" stroke-width="3"/><line x1="2" y1="31" x2="20" y2="31" stroke="#444" stroke-width="2"/><circle cx="11" cy="35" r="1.6" fill="#444"/></svg>
    <div><h3>Support Us</h3><p>We support online 24 hours a day</p></div>
  </div>
  <div class="feature" style="left:461px">
    <svg width="44" height="32" viewBox="0 0 44 32"><rect x="0" y="2" width="26" height="22" fill="#444"/><path d="M28 8h9l7 8v8H28z" fill="#444"/><circle cx="9" cy="27" r="4.5" fill="#444" stroke="#fff" stroke-width="2"/><circle cx="35" cy="27" r="4.5" fill="#444" stroke="#fff" stroke-width="2"/></svg>
    <div><h3>Free Shipping</h3><p>Express Shipping Sitewide</p></div>
  </div>
  <div class="feature" style="left:761px">
    <svg width="30" height="40" viewBox="0 0 30 40"><path d="M6 18V10a8 8 0 0 1 16 0" fill="none" stroke="#444" stroke-width="4"/><rect x="0" y="18" width="30" height="22" rx="2" fill="#444"/></svg>
    <div><h3>Security</h3><p>Lorem ipsum dolor sitconsed</p></div>
  </div>
</section>

<h2 class="section-title">Featured Products</h2>
<div class="grid">
  <div class="card"><div class="photo"><div role="img" aria-label="Pinball machine product photo"></div></div><h4>Gadget Arcade<br>Thunderwolf machines</h4><div class="price">$5000</div></div>
  <div class="card"><div class="photo"><div class="side" role="img" aria-label="Pinball machine product photo"></div></div><h4>Gadget Arcade<br>Thunderwolf machines</h4><div class="price">$8000</div></div>
  <div class="card"><div class="photo"><div class="wide" role="img" aria-label="Pinball playfield artwork"></div></div><h4>Gadget Arcade<br>Thunderwolf machines</h4><div class="price">$10,00</div></div>
  <div class="card"><div class="photo"><div class="side" role="img" aria-label="Pinball machine product photo"></div></div><h4>Gadget Arcade<br>Thunderwolf machines</h4><div class="price">$15,000</div></div>
  <div class="card"><div class="photo"><div class="wide" style="width:80px;background:linear-gradient(180deg,#2a2150,#5a3f9a 50%,#2a2150)" role="img" aria-label="Pinball playfield artwork"></div></div><h4>Gadget Arcade<br>Thunderwolf machines</h4><div class="price">$6000</div></div>
  <div class="card"><div class="photo"><div class="side" style="background:linear-gradient(180deg,#3a2a3a,#6a4a5a 40%,#1f1a22)" role="img" aria-label="Pinball machine product photo"></div></div><h4>Gadget Arcade<br>Thunderwolf machines</h4><div class="price">$15,000</div></div>
  <div class="card"><div class="photo"><div class="side" style="background:linear-gradient(180deg,#2a4050,#4a7a90 40%,#1a2530)" role="img" aria-label="Pinball machine product photo"></div></div><h4>Gadget Arcade<br>Thunderwolf machines</h4><div class="price">$8000</div></div>
  <div class="card"><div class="photo"><div class="wide" style="width:110px;background:linear-gradient(160deg,#2a3a6a,#6a3a8a 50%,#c0a040)" role="img" aria-label="Pinball playfield artwork"></div></div><h4>Gadget Arcade<br>Thunderwolf machines</h4><div class="price">$9000</div></div>
</div>

<section class="latest" role="img" aria-label="Dark photo of pinball machine internals behind the latest product">
  <svg width="1200" height="406" viewBox="0 0 1200 406"><polygon points="755,0 1093,0 990,406 597,406" fill="#ffffff"/></svg>
  <div class="text">
    <h2>Latest Products</h2>
    <p>Lorem ipsum dolor sit amet, consectetur adipiscing elit, sed do eiusmod tempor incididunt ut labore et dolore magna aliqut eni ad minim veniam, quis nostrud exercitation ullam.</p>
    <div class="price">$6000</div>
  </div>
  <div class="machine" role="img" aria-label="Latest pinball machine product photo"></div>
  <div class="dots"><i></i><i></i><i></i><i></i></div>
</section>

<section class="buy">
  <h2>We Will Buy Your Machines and Accessories!</h2>
  <p>Lorem ipsum dolor sit amet, consectetur adipiscing elit, sed do eiusmod tempor incididunt ut labore et dolore magna aliqua. Ut enim ad minim veniam, quis nostrud exercitation ullamco laboris nisi ut aliquip ex ea commLorem ipsum dolor sit amet, consectetur adipiscing elit, sed do eiusmod tempor incididunt ut labore et dolore magna aliqua. Ut enim ad minim veniam, quis nostrud exercitation ullamco laboris nisi ut aliquip ex ea commodo consequat aute irure dolo</p>
  <span class="btn">FIND OUT MORE</span>
</section>

<footer class="footer"></footer>
<div class="newsletter">
  <h3>We Buy Machines from Gadget Arcade</h3>
  <div class="field">Email Adddress:</div>
  <div class="join">JOIN US</div>
</div>

<div class="col" style="left:161px"><h4>Help &amp; Info</h4><ul><li>Track Your Order</li><li>Returns</li><li>Shipping Information</li><li>FAQs</li><li>Arcade House Credit Card</li><li>Pay Bill Online</li><li>Email Preferences</li><li>International Orders</li><li>*Promotion Details</li></ul></div>
<div class="col" style="left:392px"><h4>Stores</h4><ul><li>Locate a Store</li><li>Store Events</li><li>Free Design Services</li></ul>
  <h4 style="margin-top:18px">Resources</h4><ul><li>What's New</li><li>Gift Cards</li><li>Site Map</li></ul></div>
<div class="col" style="left:602px"><h4>Our Company</h4><ul><li>About Us</li><li>Environmental Commitment</li><li>Careers</li><li>Press</li><li>Legal Statement</li><li>Privacy Policy</li><li>Terms &amp; Conditions</li></ul></div>
<div class="dealer"><i></i><span>Vexler pinball</span></div>
<div class="follow"><h4>Follow US</h4><div><i></i><i></i><i></i><i></i><i></i><i></i></div></div>

<div class="rule"></div>
<div class="legal"><span>Privacy Policy</span><span>Terms of Use</span><span>Site Map</span><span class="chat">Live Chat</span><span>© 2017 Gadget Arcade. All Copyrights are Reserved.</span></div>

</body>
</html>
```